Satchel & Sundial needs new business card design

I need a new business card design. I'm looking for out-of-the-box design which represents the freedom of being a location independent entrepreneur.
I offer coaching, retreats and trips.
I would like to see designs with and without the photo.
Colors I use are black (#000000), green (#25A796) and brown (#D7C38C)
Website satchelandsundial.example

Target Market(s)

location independent entrepreneurs, digital nomads, people looking to swap the 9 to 5 for a lifestyle business

Industry/Entity Type

Business

Contact Information for Business Card

Dorota Falkner
Your Lifestyle Business Coach, Retreat & Trip Leader
http://satchelandsundial.example
hello@satchelandsundial.example
Live a life you don't need a holiday from

Font styles to use
Serif
Sans Serif

Requirements
Must have
• One side should contain only the logo. I would also consider having the "Live a life you don't need a holiday from" on that side too (depending on how it looks)
• Please show both sides on the designs.

```html
<!DOCTYPE html>
<html lang="en">
<head>
<meta charset="utf-8">
<title>Satchel &amp; Sundial — Business Card</title>
<link rel="stylesheet" href="https://fonts.googleapis.com/css2?family=Didact+Gothic&display=swap">
<style>
  :root {
    --ink: #1f1d1e;
    --black: #000000;
    --teal: #25a796;
    --paper: #f7f7f7;
    --card-white: #ffffff;
    --text-grey: #3a3a3a;
    --backdrop: #e9e6e0;
  }
  * { margin: 0; padding: 0; box-sizing: border-box; }
  html, body {
    width: 1200px; height: 1023px; overflow: hidden;
    background: var(--backdrop);
    font-family: "Didact Gothic", "Century Gothic", sans-serif;
  }
  .sheet { position: relative; width: 1200px; height: 1023px; }
  .card {
    position: absolute; width: 700px; height: 400px;
    box-shadow: 0 6px 18px rgba(0,0,0,.18);
    background: var(--card-white);
  }
  .card svg { display: block; width: 700px; height: 400px; }
  .card--front { left: 90px; top: 70px; }
  .card--back { left: 410px; top: 545px; }
  .brand-name { font-family: "Didact Gothic", sans-serif; }
  .person-name { fill: var(--teal); font-size: 30px; }
  .person-role { fill: var(--text-grey); font-size: 17px; }
  .contact-line { fill: var(--text-grey); font-size: 16px; }
  .tagline { fill: var(--card-white); font-size: 17px; letter-spacing: .3px; }
</style>
</head>
<body>
<main class="sheet">

  <!-- Contact side -->
  <section class="card card--front" aria-label="Business card, contact side">
    <svg viewBox="0 0 700 400" xmlns="http://www.w3.org/2000/svg">
      <rect class="card-surface" width="700" height="400" fill="var(--card-white)"/>
      <path class="accent-curve" d="M0,0 H270 C310,0 318,60 318,120 V330 C318,372 340,400 380,400 H0 Z" fill="var(--teal)"/>
      <path class="dark-panel" d="M0,0 H236 C276,0 284,60 284,120 V330 C284,372 306,400 346,400 H0 Z" fill="var(--ink)"/>

      <text class="brand-name" x="140" y="190" text-anchor="middle" font-size="38" fill="var(--card-white)">Satchel &amp;</text>
      <text class="brand-name" x="140" y="236" text-anchor="middle" font-size="38" fill="var(--card-white)">Sundial</text>

      <text class="person-name" x="350" y="66">Dorota Falkner</text>
      <text class="person-role" x="350" y="94">Your Lifestyle Business Coach,</text>
      <text class="person-role" x="350" y="116">Retreat &amp; Trip Leader</text>
      <line class="name-rule" x1="350" y1="136" x2="650" y2="136" stroke="var(--ink)" stroke-width="2"/>

      <!-- icons on accent curve -->
      <g class="icon icon-phone" fill="none" stroke="var(--card-white)" stroke-width="2" transform="translate(294,176)">
        <path d="M3,1 L7,1 L8,6 L5,8 C6,11 8,13 11,14 L13,11 L18,12 L18,16 C10,17 2,9 3,1 Z"/>
      </g>
      <g class="icon icon-mail" fill="none" stroke="var(--card-white)" stroke-width="2" transform="translate(292,238)">
        <rect x="1" y="1" width="18" height="13"/>
        <path d="M1,1 L10,9 L19,1"/>
      </g>
      <g class="icon icon-globe" fill="none" stroke="var(--card-white)" stroke-width="1.8" transform="translate(292,264)">
        <circle cx="10" cy="10" r="9"/>
        <ellipse cx="10" cy="10" rx="4" ry="9"/>
        <line x1="1" y1="10" x2="19" y2="10"/>
      </g>
      <g class="icon icon-pin" transform="translate(294,310)">
        <path d="M8,0 C13,0 16,4 16,8 C16,13 8,20 8,20 C8,20 0,13 0,8 C0,4 3,0 8,0 Z" fill="var(--card-white)"/>
        <circle cx="8" cy="8" r="3" fill="var(--teal)"/>
      </g>

      <text class="contact-line" x="350" y="190">555-014-2736</text>
      <text class="contact-line" x="350" y="212">555-014-2737</text>
      <text class="contact-line" x="350" y="252">hello@satchelandsundial.example</text>
      <text class="contact-line" x="350" y="278">www.satchelandsundial.example</text>
      <text class="contact-line" x="350" y="318">Here your company or</text>
      <text class="contact-line" x="350" y="340">home address</text>
    </svg>
  </section>

  <!-- Logo side -->
  <section class="card card--back" aria-label="Business card, logo side">
    <svg viewBox="0 0 700 400" xmlns="http://www.w3.org/2000/svg">
      <rect class="card-surface" width="700" height="400" fill="var(--paper)"/>
      <path class="accent-band" d="M0,292 H300 C330,292 338,274 370,274 H700 V330 H0 Z" fill="var(--teal)"/>
      <text class="brand-name" x="350" y="170" text-anchor="middle" font-size="50" fill="var(--ink)">Satchel &amp; Sundial</text>
      <text class="tagline" x="390" y="308">Live a life you don't need a holiday from</text>
    </svg>
  </section>

</main>
</body>
</html>
```